Spring Detox sale graphics for social media

You MUST read the Brief in the WORD document and follow the instructions there. I want to create 10 social media graphics (new Instagram size 4:5 (1080 x 1350 pixels) focusing on our Mother’s Day Spring Detox Sale graphics, using any of the pics attached. Use the attached pics, NO RANDOM STOCK PHOTOGRAPHY. For the color scheme of the graphics, they should all be complementary to the product colors or feel like Spring time.

Target Market(s)

primarily women

Requirements
Must have
• the photos and text attached

```html
<!DOCTYPE html>
<html lang="en">
<head>
<meta charset="utf-8">
<title>Mother's Day Spring Detox Sale – Social Set</title>
<link rel="stylesheet" href="https://fonts.googleapis.com/css2?family=Oswald:wght@600;700&family=Montserrat:wght@600;700;800&display=swap">
<style>
  :root {
    --board: #000000;
    --paper: #ffffff;
    --blush: #fdf6f6;
    --mint: #eefbf0;
    --ice: #eef9fd;
    --cream: #fdf5ee;
    --forest: #2a5e2e;
    --rose: #e0519a;
    --rose-deep: #d81b7a;
    --plum: #7a3a5a;
    --violet: #8a1a9a;
    --orchid: #9b3a9b;
    --navy: #1c2a8c;
    --navy-deep: #1a1a5a;
    --wine: #7a1020;
    --scarlet: #f0142a;
    --teal: #1f8a70;
    --teal-deep: #1a7a66;
    --slate: #2e4a44;
    --leaf: #1a8a1a;
    --pine: #2a6e4e;
    --bubble: #f78fb0;
    --berry: #c21a6a;
  }
  html, body { margin: 0; padding: 0; width: 1200px; height: 2652px; overflow: hidden; background: var(--board); }
  .board { display: block; width: 1200px; height: 2652px; }
  .cond { font-family: "Oswald", "Arial Narrow", sans-serif; font-weight: 700; }
  .sans { font-family: "Montserrat", "Helvetica", sans-serif; font-weight: 700; }
  .sans-semi { font-family: "Montserrat", "Helvetica", sans-serif; font-weight: 600; }
  .sans-heavy { font-family: "Montserrat", "Helvetica", sans-serif; font-weight: 800; }
</style>
</head>
<body>
<svg class="board" viewBox="0 0 1166 2576" xmlns="http://www.w3.org/2000/svg">
  <defs>
    <linearGradient id="bottle-tone" x1="0" y1="0" x2="0" y2="1">
      <stop offset="0" stop-color="#f4f4f4"/>
      <stop offset="0.6" stop-color="#e3e3e6"/>
      <stop offset="1" stop-color="#c9c9d2"/>
    </linearGradient>
  </defs>
  <rect width="1166" height="2576" fill="var(--board)"/>

  <!-- Post 1 -->
  <g class="post post-1">
    <rect x="240" y="209" width="335" height="418" fill="var(--blush)"/>
    <path d="M400 627 Q470 560 575 540 L575 627 Z" fill="#fbeff1"/>
    <text class="cond" x="282" y="305" font-size="49" textLength="250" lengthAdjust="spacingAndGlyphs" fill="var(--forest)">MOTHER’S DAY</text>
    <text class="cond" x="282" y="400" font-size="98" textLength="252" lengthAdjust="spacingAndGlyphs" fill="var(--rose)">SPRING</text>
    <text class="cond" x="282" y="472" font-size="68" textLength="250" lengthAdjust="spacingAndGlyphs" fill="var(--rose)">Detox Sale</text>
    <text class="cond" x="282" y="566" font-size="96" textLength="88" lengthAdjust="spacingAndGlyphs" fill="var(--forest)">25</text>
    <text class="cond" x="378" y="527" font-size="50" textLength="40" lengthAdjust="spacingAndGlyphs" fill="var(--forest)">%</text>
    <text class="cond" x="378" y="567" font-size="36" textLength="45" lengthAdjust="spacingAndGlyphs" fill="var(--forest)">OFF</text>
    <text class="sans" x="428" y="534" font-size="18" textLength="104" lengthAdjust="spacingAndGlyphs" fill="var(--forest)">Everything!</text>
  </g>

  <!-- Post 2 -->
  <g class="post post-2">
    <rect x="589" y="209" width="335" height="418" fill="var(--mint)"/>
    <rect x="630" y="218" width="260" height="107" rx="10" fill="url(#bottle-tone)" role="img" aria-label="Product photo: row of four supplement bottles"/>
    <text class="cond" x="653" y="406" font-size="78" textLength="75" lengthAdjust="spacingAndGlyphs" fill="var(--navy)">25</text>
    <text class="cond" x="735" y="372" font-size="40" textLength="32" lengthAdjust="spacingAndGlyphs" fill="var(--navy)">%</text>
    <text class="cond" x="735" y="407" font-size="32" textLength="38" lengthAdjust="spacingAndGlyphs" fill="var(--navy)">OFF</text>
    <text class="cond" x="653" y="458" font-size="46" textLength="203" lengthAdjust="spacingAndGlyphs" fill="var(--navy)">Mother’s Day</text>
    <text class="cond" x="653" y="528" font-size="92" textLength="204" lengthAdjust="spacingAndGlyphs" fill="var(--orchid)">Spring</text>
    <text class="cond" x="653" y="597" font-size="54" textLength="204" lengthAdjust="spacingAndGlyphs" fill="var(--orchid)">DETOX SALE</text>
  </g>

  <!-- Post 3 -->
  <g class="post post-3">
    <rect x="240" y="643" width="335" height="418" fill="var(--paper)"/>
    <path d="M240 940 L575 740 L575 1061 L240 1061 Z" fill="var(--ice)"/>
    <text class="cond" x="322" y="795" font-size="108" textLength="106" lengthAdjust="spacingAndGlyphs" fill="var(--plum)">25</text>
    <text class="cond" x="437" y="750" font-size="48" textLength="46" lengthAdjust="spacingAndGlyphs" fill="var(--plum)">%</text>
    <text class="cond" x="437" y="797" font-size="44" textLength="52" lengthAdjust="spacingAndGlyphs" fill="var(--plum)">OFF</text>
    <text class="sans-semi" x="282" y="835" font-size="30" textLength="252" lengthAdjust="spacingAndGlyphs" fill="var(--plum)">All Supplements</text>
    <text class="cond" x="282" y="935" font-size="100" textLength="248" lengthAdjust="spacingAndGlyphs" fill="var(--rose)">SPRING</text>
    <text class="cond" x="282" y="1000" font-size="66" textLength="250" lengthAdjust="spacingAndGlyphs" fill="var(--rose)">DETOX SALE</text>
  </g>

  <!-- Post 4 -->
  <g class="post post-4">
    <rect x="589" y="643" width="335" height="418" fill="var(--paper)"/>
    <text class="cond" x="601" y="755" font-size="96" textLength="90" lengthAdjust="spacingAndGlyphs" fill="var(--violet)">25</text>
    <text class="cond" x="700" y="718" font-size="42" textLength="38" lengthAdjust="spacingAndGlyphs" fill="var(--violet)">%</text>
    <text class="cond" x="700" y="756" font-size="38" textLength="45" lengthAdjust="spacingAndGlyphs" fill="var(--violet)">OFF</text>
    <rect x="758" y="677" width="154" height="93" rx="8" fill="url(#bottle-tone)" role="img" aria-label="Product photo: four supplement bottles"/>
    <text class="cond" x="649" y="823" font-size="46" textLength="204" lengthAdjust="spacingAndGlyphs" fill="var(--rose-deep)">SPRING DETOX</text>
    <text class="cond" x="649" y="932" font-size="132" textLength="206" lengthAdjust="spacingAndGlyphs" fill="var(--rose-deep)">SALE</text>
    <text class="sans-heavy" x="649" y="973" font-size="30" textLength="212" lengthAdjust="spacingAndGlyphs" fill="var(--violet)">Spring  Reset</text>
    <text class="sans-heavy" x="649" y="1005" font-size="28" textLength="212" lengthAdjust="spacingAndGlyphs" fill="var(--violet)">Summer  Ready</text>
  </g>

  <!-- Post 5 -->
  <g class="post post-5">
    <rect x="240" y="1078" width="335" height="418" fill="var(--paper)"/>
    <text class="cond" x="288" y="1213" font-size="92" textLength="84" lengthAdjust="spacingAndGlyphs" fill="var(--wine)">25</text>
    <text class="cond" x="378" y="1180" font-size="44" textLength="36" lengthAdjust="spacingAndGlyphs" fill="var(--wine)">%</text>
    <text class="cond" x="378" y="1214" font-size="34" textLength="40" lengthAdjust="spacingAndGlyphs" fill="var(--wine)">OFF</text>
    <text class="sans" x="430" y="1186" font-size="17" textLength="96" lengthAdjust="spacingAndGlyphs" fill="var(--wine)">Everything!</text>
    <text class="cond" x="291" y="1270" font-size="48" textLength="232" lengthAdjust="spacingAndGlyphs" fill="var(--wine)">MOTHER’S DAY</text>
    <text class="cond" x="291" y="1358" font-size="98" textLength="234" lengthAdjust="spacingAndGlyphs" fill="var(--scarlet)">SPRING</text>
    <text class="cond" x="291" y="1415" font-size="66" textLength="236" lengthAdjust="spacingAndGlyphs" fill="var(--scarlet)">DETOX SALE</text>
  </g>

  <!-- Post 6 -->
  <g class="post post-6">
    <rect x="590" y="1078" width="335" height="418" fill="var(--paper)"/>
    <text class="cond" x="682" y="1185" font-size="80" textLength="88" lengthAdjust="spacingAndGlyphs" fill="var(--teal)">25</text>
    <text class="cond" x="773" y="1150" font-size="44" textLength="36" lengthAdjust="spacingAndGlyphs" fill="var(--teal)">%</text>
    <text class="cond" x="775" y="1187" font-size="32" textLength="58" lengthAdjust="spacingAndGlyphs" fill="var(--teal)">OFF</text>
    <text class="cond" x="659" y="1231" font-size="44" textLength="196" lengthAdjust="spacingAndGlyphs" fill="var(--slate)">MOTHER’S DAY</text>
    <text class="cond" x="660" y="1333" font-size="122" textLength="195" lengthAdjust="spacingAndGlyphs" fill="var(--slate)">SALE</text>
    <text class="cond" x="657" y="1375" font-size="46" textLength="200" lengthAdjust="spacingAndGlyphs" fill="var(--teal)">FEEL AMAZING</text>
    <text class="cond" x="651" y="1452" font-size="92" textLength="213" lengthAdjust="spacingAndGlyphs" fill="var(--teal-deep)">AGAIN!</text>
  </g>

  <!-- Post 7 -->
  <g class="post post-7">
    <rect x="241" y="1512" width="335" height="418" fill="var(--paper)"/>
    <text class="cond" x="328" y="1625" font-size="100" textLength="92" lengthAdjust="spacingAndGlyphs" fill="var(--leaf)">25</text>
    <text class="cond" x="427" y="1583" font-size="50" textLength="40" lengthAdjust="spacingAndGlyphs" fill="var(--leaf)">%</text>
    <text class="cond" x="427" y="1627" font-size="40" textLength="46" lengthAdjust="spacingAndGlyphs" fill="var(--leaf)">OFF</text>
    <text class="cond" x="283" y="1703" font-size="76" textLength="250" lengthAdjust="spacingAndGlyphs" fill="var(--navy)">MOTHER’S</text>
    <text class="cond" x="290" y="1767" font-size="76" textLength="234" lengthAdjust="spacingAndGlyphs" fill="var(--navy)">DAY SALE</text>
    <text class="cond" x="316" y="1833" font-size="66" textLength="186" lengthAdjust="spacingAndGlyphs" fill="var(--leaf)">REFRESH</text>
    <text class="cond" x="283" y="1888" font-size="66" textLength="252" lengthAdjust="spacingAndGlyphs" fill="var(--leaf)">YOUR BODY</text>
  </g>

  <!-- Post 8 -->
  <g class="post post-8">
    <rect x="589" y="1512" width="335" height="418" fill="var(--cream)"/>
    <circle cx="848" cy="1594" r="52" fill="var(--bubble)"/>
    <text class="cond" x="810" y="1615" font-size="56" textLength="48" lengthAdjust="spacingAndGlyphs" fill="var(--paper)">25</text>
    <text class="cond" x="862" y="1594" font-size="24" textLength="20" lengthAdjust="spacingAndGlyphs" fill="var(--paper)">%</text>
    <text class="cond" x="862" y="1614" font-size="20" textLength="24" lengthAdjust="spacingAndGlyphs" fill="var(--paper)">OFF</text>
    <text class="cond" x="651" y="1664" font-size="48" textLength="220" lengthAdjust="spacingAndGlyphs" fill="var(--pine)">SPRING DETOX</text>
    <text class="cond" x="653" y="1770" font-size="130" textLength="220" lengthAdjust="spacingAndGlyphs" fill="var(--pine)">SALE</text>
    <text class="cond" x="644" y="1826" font-size="48" textLength="236" lengthAdjust="spacingAndGlyphs" fill="var(--pine)">Spring Cleanse</text>
    <text class="cond" x="640" y="1876" font-size="52" textLength="240" lengthAdjust="spacingAndGlyphs" fill="var(--pine)">Summer Glow</text>
  </g>

  <!-- Post 9 -->
  <g class="post post-9">
    <rect x="241" y="1947" width="335" height="418" fill="var(--paper)"/>
    <text class="cond" x="332" y="2078" font-size="102" textLength="93" lengthAdjust="spacingAndGlyphs" fill="var(--navy)">25</text>
    <text class="cond" x="432" y="2038" font-size="48" textLength="40" lengthAdjust="spacingAndGlyphs" fill="var(--navy)">%</text>
    <text class="cond" x="432" y="2080" font-size="40" textLength="47" lengthAdjust="spacingAndGlyphs" fill="var(--navy)">OFF</text>
    <text class="cond" x="296" y="2136" font-size="48" textLength="222" lengthAdjust="spacingAndGlyphs" fill="var(--navy-deep)">MOTHER’S DAY</text>
    <text class="cond" x="300" y="2246" font-size="132" textLength="210" lengthAdjust="spacingAndGlyphs" fill="var(--navy)">SALE</text>
    <text class="sans-semi" x="307" y="2284" font-size="24" textLength="210" lengthAdjust="spacingAndGlyphs" fill="var(--navy-deep)">Detox This Spring.</text>
    <text class="sans-semi" x="302" y="2312" font-size="24" textLength="220" lengthAdjust="spacingAndGlyphs" fill="var(--navy-deep)">Shine This Summer</text>
  </g>

  <!-- Post 10 -->
  <g class="post post-10">
    <rect x="589" y="1947" width="335" height="418" fill="var(--paper)"/>
    <text class="cond" x="623" y="2066" font-size="88" textLength="82" lengthAdjust="spacingAndGlyphs" fill="var(--leaf)">25</text>
    <text class="cond" x="708" y="2032" font-size="42" textLength="34" lengthAdjust="spacingAndGlyphs" fill="var(--leaf)">%</text>
    <text class="cond" x="708" y="2067" font-size="34" textLength="40" lengthAdjust="spacingAndGlyphs" fill="var(--leaf)">OFF</text>
    <rect x="752" y="1972" width="170" height="88" rx="8" fill="url(#bottle-tone)" role="img" aria-label="Product photo: four supplement bottles"/>
    <text class="cond" x="623" y="2112" font-size="52" textLength="240" lengthAdjust="spacingAndGlyphs" fill="var(--navy)">MOTHER’S DAY</text>
    <text class="cond" x="623" y="2235" font-size="140" textLength="238" lengthAdjust="spacingAndGlyphs" fill="var(--navy)">SALE</text>
    <text class="cond" x="623" y="2290" font-size="58" textLength="240" lengthAdjust="spacingAndGlyphs" fill="var(--berry)">Spring Detox</text>
    <text class="cond" x="623" y="2333" font-size="40" textLength="240" lengthAdjust="spacingAndGlyphs" fill="var(--berry)">for a Summer Body</text>
  </g>
</svg>
</body>
</html>
```